Business Card Design

We need a business card design for a Dry cleaners in Brisbane, Australia. We are trying to promote a fresh/clean image consistent with our website. www.pinnelgarmentcare.com.au

Looking for a professional neat card that's easy to read.

Target Market(s)

Customers looking for a professional, fresh and clean drycleaners.

Industry/Entity Type

Business

Contact Information for Business Card

See our existing business card. The Fax number (07) 3468 5270 to be removed.

Requirements
Must have
• All the details on current business card less the fax number.
Nice to have
• I like white text on coloured background. Blue works well as we are located near the water...

```html
<!DOCTYPE html>
<html lang="en">
<head>
<meta charset="utf-8">
<title>Pinnel Garment Care – Business Card</title>
<link href="https://fonts.googleapis.com/css2?family=Open+Sans:wght@400;700&display=swap" rel="stylesheet">
<style>
  :root {
    --page: #ffffff;
    --card-blue: #0414da;
    --wave-band: #1e2fd6;
    --wave-light: #135ae0;
    --text: #ffffff;
  }
  html, body {
    margin: 0;
    padding: 0;
    width: 1200px;
    height: 1000px;
    overflow: hidden;
    background: var(--page);
    font-family: "Open Sans", Arial, sans-serif;
  }
  .card {
    position: absolute;
    left: 45px;
    top: 157px;
    width: 1110px;
    height: 685px;
    background: var(--card-blue);
    color: var(--text);
    overflow: hidden;
  }
  .card-wave {
    position: absolute;
    left: 0;
    top: 0;
    width: 1110px;
    height: 685px;
  }
  .brand-name {
    position: absolute;
    left: 95px;
    top: 150px;
    margin: 0;
    font-size: 58px;
    font-weight: 700;
    letter-spacing: 0.5px;
    line-height: 1;
  }
  .contact-person {
    position: absolute;
    left: 92px;
    top: 352px;
  }
  .person-name {
    margin: 0 0 6px;
    font-size: 38px;
    font-weight: 700;
    line-height: 1.1;
  }
  .person-line {
    margin: 0;
    font-size: 28px;
    line-height: 35px;
  }
  .contact-shop {
    position: absolute;
    left: 746px;
    top: 354px;
  }
  .shop-line {
    margin: 0;
    font-size: 31px;
    line-height: 40px;
  }
  .locations {
    position: absolute;
    left: 0;
    width: 1110px;
    top: 590px;
    margin: 0;
    text-align: center;
    font-size: 43px;
    line-height: 60px;
  }
  .locations .divider {
    padding: 0 40px;
  }
</style>
</head>
<body>
  <main class="card">
    <svg class="card-wave" viewBox="0 0 1110 685" aria-hidden="true">
      <path d="M0,532 C250,470 500,505 720,560 C860,592 1000,550 1110,482 L1110,685 L0,685 Z" fill="var(--wave-band)"/>
      <path d="M0,556 C250,490 500,525 720,578 C860,608 1000,570 1110,502 L1110,685 L0,685 Z" fill="var(--wave-light)"/>
    </svg>

    <h1 class="brand-name">Pinnel Garment Care</h1>

    <section class="contact-person">
      <p class="person-name">Jordan Kessler</p>
      <p class="person-line">M: 0412 587 034</p>
      <p class="person-line">E: jordan@pinnelgarmentcare.com.au</p>
    </section>

    <section class="contact-shop">
      <p class="shop-line">18 Marlow St</p>
      <p class="shop-line">Seabrook Qld 4189</p>
      <p class="shop-line">P: (07) 3521 4806</p>
    </section>

    <p class="locations">Seabrook<span class="divider">|</span>Harlow Bay<span class="divider">|</span>Marlin Pt</p>
  </main>
</body>
</html>
```